A start-up named "Corvane Therapeutics" - needs a new PowerPoint design

We need a new PowerPoint Design for an early-stage start-up named "Corvane Therapeutics" seeking to disrupt the current approach towards drug discovery within aging disorders.

We would like to build on Corvane's legacy, the founder of the modern science of genetics, by employing a multidisciplinary approach, experimenting, and providing elderly patients the attention they deserve.

We have selected the suffix "therapeutics" intentionally as it stands for (a medicine) the treatment of disease; the science of healing. Alzheimer’s treatment is a huge, urgent, unmet need:
- Shift from a disease-management system to a preventive medicine system
- Focus on increasing the health span, not only the life span

Target Market(s)

Pharma/ Biotech Executives Medical Institutions Healthcare professionals (MDs, nurses, payors, pharmacists, etc.) Patients

Industry/Entity Type

Healthcare

Other font styles liked:
• Celias

Colors
0054AA
0677BA
7BADD7
CADEEF
E8F1F8
E54698
E96AAD
F1A4CE
F9D9EA
FCEFF6
A7469A
B969AE
D3A5CF
EDDBEB
F8F0F9
6B429C
8869AF
B7A5CE
E3DAEB
F3F0F8

Requirements
Must have
• - differentiate from other companies named after Corvane - differentiate from other Pharma/ Biotech companies
Nice to have
• simplicity/ minimalist logo vivid colors gradient 3D Life-Sciences inspired Simple geometry Balance
Should not have
• mascot/ emblem watermark logo animated ink style nature-inspired inventive typography artistic chaos

```html
<!DOCTYPE html>
<html lang="en">
<head>
<meta charset="utf-8">
<title>Corvane Therapeutics — Presentation Template</title>
<link href="https://fonts.googleapis.com/css2?family=Montserrat:wght@400;500;600&display=swap" rel="stylesheet">
<style>
:root{
  --page:#a3a3a3;
  --blue:#1e8cff;
  --blue-deep:#2a6fe0;
  --indigo:#4e6fe8;
  --purple:#b70ff0;
  --crimson:#d9416f;
  --navy:#2f3b55;
  --ink:#3a3f4a;
  --body:#5a5e66;
  --rule:#e3e5ea;
  --panel:#f4f5f7;
  --dark:#17181c;
  --grad:linear-gradient(90deg,var(--blue),var(--purple));
}
*{box-sizing:border-box;margin:0;padding:0}
html,body{width:890px;height:1200px;overflow:hidden;background:var(--page);font-family:'Montserrat',sans-serif}
.deck{display:grid;grid-template-columns:repeat(3,272px);grid-auto-rows:153px;gap:13px;padding:25px 0 0 24px}
.slide{position:relative;width:272px;height:153px;background:#fff;overflow:hidden;color:var(--ink)}
.abs{position:absolute}
.slide-title{position:absolute;left:14px;top:11px;font-size:10.4px;font-weight:500;color:var(--ink);letter-spacing:-.1px}
.brand{position:absolute;right:14px;top:14px;display:flex;align-items:center;gap:2px;color:var(--blue-deep)}
.brand-mark{width:7px;height:7px;border:1.2px solid currentColor}
.brand-name{font-size:5.4px;font-weight:500;line-height:.95}
.brand-name small{display:block;font-size:2.3px;letter-spacing:.1px}
.footer{position:absolute;left:0;right:0;bottom:0;height:5px;background:var(--grad);color:#fff;font-size:2px;display:flex;justify-content:space-between;align-items:center;padding:0 3px}
.lorem{font-size:3px;line-height:1.3;color:var(--body)}
.center{text-align:center}
.photo{position:absolute}
.t-blue{color:var(--blue)} .t-purple{color:var(--purple)} .t-crimson{color:var(--crimson)} .t-indigo{color:var(--indigo)}
.bullets{list-style:none}
.bullets li{position:relative;padding-left:5px;margin-bottom:2.5px}
.bullets li::before{content:"";position:absolute;left:0;top:1px;width:1.4px;height:1.4px;border-radius:50%;background:var(--blue)}
.ticks{list-style:none;font-size:2.8px;line-height:1.3;color:var(--body)}
.ticks li::before{content:"✓ ";color:var(--purple)}

/* title slides */
.cover-title{position:absolute;left:17px;top:64px;font-size:14px;line-height:1.05;font-weight:500}
.cover-date{position:absolute;left:17px;top:104px;font-size:2.8px}
.cover-brand{position:absolute;left:17px;top:31px;display:flex;align-items:center;gap:3px}
.cover-brand .brand-mark{width:13px;height:13px;border-width:1.6px}
.cover-brand .brand-name{font-size:9px}
.cover-brand .brand-name small{font-size:3.4px}
.cover-foot{position:absolute;left:0;right:0;bottom:0;height:11px;background:#f1f1f1;font-size:2.2px;color:#888;text-align:center;line-height:11px}

/* agenda */
.agenda-item{position:absolute;width:90px;display:flex;gap:6px}
.agenda-num{font-size:9px;font-weight:400;color:#c9cbd0;width:8px;line-height:1}
.agenda-item h4{font-size:5.4px;font-weight:500;color:var(--blue);margin-bottom:1px}

.person-name{font-size:5.4px;font-weight:500;color:var(--blue);line-height:1.05}
.person-role{font-size:2.6px;color:var(--body);margin:1.5px 0}
.avatar{position:absolute;border-radius:50%;background:radial-gradient(circle at 50% 40%,#c9b6a4,#8c8f96 70%)}
.portrait{position:absolute;width:34px;height:50px;background:linear-gradient(180deg,#d6d8dc,#a99686 55%,#5c5e64)}
.team-card{position:absolute;width:34px;text-align:center}
.team-card .person-name{font-size:5px}
.team-card .lorem{font-size:2.3px}

.icon-dot{position:absolute;width:20px;height:20px;border-radius:50%;display:flex;align-items:center;justify-content:center}
.feature{position:absolute;width:52px;text-align:center}
.feature h4{font-size:5px;font-weight:500;margin-bottom:2px}
.feature .lorem{font-size:2.5px}

.col-head{font-size:5px;font-weight:500;color:var(--blue);margin-bottom:5px}

.step{position:absolute;width:12px;height:12px;border-radius:50%;color:#fff;font-size:6px;display:flex;align-items:center;justify-content:center;border:1px solid #fff;box-shadow:0 0 0 .6px #ddd}
.step-label{position:absolute;width:40px;text-align:center;font-size:4.4px;line-height:1.05}

.side-tab{position:absolute;width:12px;color:#fff;font-size:5px;display:flex;align-items:center;justify-content:center}
.side-tab span{transform:rotate(-90deg)}
.pie-note{position:absolute;width:88px;text-align:center}
.pie-note h4{font-size:5px;font-weight:500;margin-bottom:1.5px}
.pie-note .lorem{font-size:2.5px}

.table{position:absolute;left:19px;top:42px;width:234px;border-collapse:collapse;font-size:2.8px}
.table td,.table th{border:.5px solid #fff;text-align:center}
.table .row td{border-bottom:.4px solid var(--rule);height:8.4px;color:#e0e0e0}
.table .row td:first-child{text-align:left;color:var(--ink);padding-left:2px}
.table .row td.tick-b{color:var(--blue)} .table .row td.tick-p{color:var(--purple)}

.quote-box{position:absolute;top:41px;width:79px;height:89px;color:#fff;padding:6px 9px}
.quote-box .mark{font-size:16px;line-height:1;font-weight:600}
.quote-box p{font-size:3.9px;line-height:1.25;margin-top:6px}
</style>
</head>
<body>
<main class="deck">

<!-- 1 cover light -->
<section class="slide">
  <svg class="abs" width="272" height="153" viewBox="0 0 272 153">
    <defs><linearGradient id="coverPhotoA" x1="0" y1="0" x2="1" y2="1"><stop offset="0" stop-color="#e8e6ea"/><stop offset=".5" stop-color="#d9d3d8"/><stop offset="1" stop-color="#b7b2bf"/></linearGradient></defs>
    <rect x="60" y="0" width="212" height="142" fill="url(#coverPhotoA)" role="img" aria-label="Photo of a pharmacist in a mask working in a pharmacy"/>
    <polygon points="74,0 125,0 211,76 160,76" fill="#1e8cff" opacity=".45"/>
    <polygon points="106,142 160,76 211,76 157,142" fill="#b70ff0" opacity=".35"/>
    <polygon points="0,0 74,0 160,76 106,142 0,142" fill="#fff"/>
  </svg>
  <div class="cover-brand" style="color:var(--blue-deep)"><span class="brand-mark"></span><span class="brand-name">Corvane<small>Therapeutics</small></span></div>
  <h1 class="cover-title" style="color:var(--ink)">Corvane<br>Therapeutics</h1>
  <p class="cover-date">Monday, February 7, 2022</p>
  <div class="cover-foot">© 2021 Corvane Therapeutics. All Rights Reserved.</div>
</section>

<!-- 2 cover dark -->
<section class="slide">
  <svg class="abs" width="272" height="153" viewBox="0 0 272 153">
    <defs><linearGradient id="coverPhotoB" x1="0" y1="0" x2="1" y2="1"><stop offset="0" stop-color="#c9d4dc"/><stop offset=".5" stop-color="#5d8fb8"/><stop offset="1" stop-color="#8a6fa5"/></linearGradient></defs>
    <rect x="60" y="0" width="212" height="142" fill="url(#coverPhotoB)" role="img" aria-label="Photo of a scientist pipetting samples in a laboratory"/>
    <polygon points="106,142 160,76 211,76 157,142" fill="#b70ff0" opacity=".35"/>
    <polygon points="0,0 74,0 160,76 106,142 0,142" fill="#000"/>
  </svg>
  <div class="cover-brand" style="color:#fff"><span class="brand-mark"></span><span class="brand-name">Corvane<small>Therapeutics</small></span></div>
  <h1 class="cover-title" style="color:#fff">Corvane<br>Therapeutics</h1>
  <p class="cover-date" style="color:#fff">Monday, February 7, 2022</p>
  <div class="cover-foot">© 2021 Corvane Therapeutics. All Rights Reserved.</div>
</section>

<!-- 3 cover blue -->
<section class="slide">
  <svg class="abs" width="272" height="153" viewBox="0 0 272 153">
    <defs><linearGradient id="coverPhotoC" x1="0" y1="0" x2="1" y2="1"><stop offset="0" stop-color="#9aa6b8"/><stop offset=".6" stop-color="#c6c9cf"/><stop offset="1" stop-color="#6f7f96"/></linearGradient></defs>
    <rect x="60" y="0" width="212" height="142" fill="url(#coverPhotoC)" role="img" aria-label="Photo of hands holding a tablet"/>
    <polygon points="106,142 160,76 211,76 157,142" fill="#b70ff0" opacity=".35"/>
    <polygon points="0,0 74,0 160,76 106,142 0,142" fill="#1e8cff"/>
  </svg>
  <div class="cover-brand" style="color:#fff"><span class="brand-mark"></span><span class="brand-name">Corvane<small>Therapeutics</small></span></div>
  <h1 class="cover-title" style="color:#fff">Corvane<br>Therapeutics</h1>
  <p class="cover-date" style="color:#fff">Monday, February 7, 2022</p>
  <div class="cover-foot">© 2021 Corvane Therapeutics. All Rights Reserved.</div>
</section>

<!-- 4 agenda -->
<section class="slide">
  <h2 class="slide-title">Agenda Slide</h2>
  <div class="brand"><span class="brand-mark"></span><span class="brand-name">Corvane<small>Therapeutics</small></span></div>
  <div class="agenda-item" style="left:36px;top:50px"><span class="agenda-num">1</span><div><h4>Title Goes Here</h4><p class="lorem">Lorem ipsum dolor sit amet, consectetur adipiscing elit. Vivamus eu dui ex.</p></div></div>
  <div class="agenda-item" style="left:143px;top:50px"><span class="agenda-num">2</span><div><h4>Title Goes Here</h4><p class="lorem">Lorem ipsum dolor sit amet, consectetur adipiscing elit. Vivamus eu dui ex.</p></div></div>
  <div class="agenda-item" style="left:36px;top:77px"><span class="agenda-num">3</span><div><h4>Title Goes Here</h4><p class="lorem">Lorem ipsum dolor sit amet, consectetur adipiscing elit. Vivamus eu dui ex.</p></div></div>
  <div class="agenda-item" style="left:143px;top:77px"><span class="agenda-num">4</span><div><h4>Title Goes Here</h4><p class="lorem">Lorem ipsum dolor sit amet, consectetur adipiscing elit. Vivamus eu dui ex.</p></div></div>
  <div class="agenda-item" style="left:36px;top:104px"><span class="agenda-num">5</span><div><h4>Title Goes Here</h4><p class="lorem">Lorem ipsum dolor sit amet, consectetur adipiscing elit. Vivamus eu dui ex.</p></div></div>
  <div class="agenda-item" style="left:143px;top:104px"><span class="agenda-num">6</span><div><h4>Title Goes Here</h4><p class="lorem">Lorem ipsum dolor sit amet, consectetur adipiscing elit. Vivamus eu dui ex.</p></div></div>
  <div class="footer"><span>© 2021 Corvane Therapeutics. All Rights Reserved.</span><span>4</span></div>
</section>

<!-- 5 about -->
<section class="slide">
  <div class="photo" style="left:17px;top:0;width:126px;height:82px;background:linear-gradient(135deg,#cfdbe6,#5f86a8 60%,#2c4d72)" role="img" aria-label="Photo of a scientist at a lab bench with monitors"></div>
  <div class="photo" style="left:17px;top:86px;width:62px;height:40px;background:linear-gradient(135deg,#e4e2e6,#a8a4b0)" role="img" aria-label="Photo of a researcher using a tablet"></div>
  <div class="photo" style="left:81px;top:86px;width:62px;height:40px;background:linear-gradient(135deg,#e8ecef,#b4c2cf)" role="img" aria-label="Photo of a pharmacist in a lab coat"></div>
  <div class="brand"><span class="brand-mark"></span><span class="brand-name">Corvane<small>Therapeutics</small></span></div>
  <h2 class="abs" style="left:155px;top:42px;font-size:10px;font-weight:500">About Us</h2>
  <p class="lorem abs" style="left:155px;top:56px;width:100px">Lorem ipsum dolor sit amet, consectetur adipiscing elit. Vivamus eu dui ex. Curabitur dapibus dignissim dui, in molestie metus feugiat sed. Praesent aliquet lorem ex, eu dapibus.</p>
  <ul class="bullets lorem abs" style="left:155px;top:77px;width:100px">
    <li>Lorem ipsum dolor sit amet, consectetur adipiscing elit. Vivamus eu dui ex.</li>
    <li>Curabitur dapibus dignissim dui, in molestie metus feugiat sed.</li>
    <li>Praesent aliquet lorem ex, eu dapibus odio varius at. Duis eget tellus porta, consequat lacus vitae, venenatis dolor.</li>
    <li>Nulla facilisi. In et sollicitudin lacus. Donec risus orci, gravida sit amet risus vehicular.</li>
  </ul>
  <div class="footer"><span>© 2021 Corvane Therapeutics. All Rights Reserved.</span><span>5</span></div>
</section>

<!-- 6 team -->
<section class="slide">
  <h2 class="slide-title">Meet Our Team</h2>
  <div class="brand"><span class="brand-mark"></span><span class="brand-name">Corvane<small>Therapeutics</small></span></div>
  <div class="avatar" style="left:36px;top:44px;width:36px;height:36px" role="img" aria-label="Team member portrait"></div>
  <div class="avatar" style="left:118px;top:44px;width:36px;height:36px" role="img" aria-label="Team member portrait"></div>
  <div class="avatar" style="left:199px;top:44px;width:36px;height:36px" role="img" aria-label="Team member portrait"></div>
  <div class="abs center" style="left:20px;top:86px;width:68px"><p class="person-name">Name Goes Here</p><p class="person-role">Job Title Goes Here</p><p class="lorem">Lorem ipsum dolor sit amet, consectetur adipiscing elit. Vivamus eu dui ex. Curabitur dapibus dignissim dui, in molestie metus feugiat sed.</p></div>
  <div class="abs center" style="left:102px;top:86px;width:68px"><p class="person-name">Name Goes Here</p><p class="person-role">Job Title Goes Here</p><p class="lorem">Lorem ipsum dolor sit amet, consectetur adipiscing elit. Vivamus eu dui ex. Curabitur dapibus dignissim dui, in molestie metus feugiat sed.</p></div>
  <div class="abs center" style="left:183px;top:86px;width:68px"><p class="person-name">Name Goes Here</p><p class="person-role">Job Title Goes Here</p><p class="lorem">Lorem ipsum dolor sit amet, consectetur adipiscing elit. Vivamus eu dui ex. Curabitur dapibus dignissim dui, in molestie metus feugiat sed.</p></div>
  <div class="footer"><span>© 2021 Corvane Therapeutics. All Rights Reserved.</span><span>6</span></div>
</section>

<!-- 7 team grid -->
<section class="slide">
  <h2 class="slide-title">Meet Our Team</h2>
  <div class="brand"><span class="brand-mark"></span><span class="brand-name">Corvane<small>Therapeutics</small></span></div>
  <div class="team-card" style="left:14px;top:38px"><p class="person-name">Name<br>Goes Here</p><p class="person-role">Job Title Goes Here</p><p class="lorem">Lorem ipsum dolor sit amet, consectetur adipiscing elit. Vivamus eu dui ex. Curabitur dapibus dignissim dui.</p></div>
  <div class="portrait" style="left:56px;top:38px" role="img" aria-label="Team member portrait"></div>
  <div class="team-card" style="left:98px;top:38px"><p class="person-name">Name<br>Goes Here</p><p class="person-role">Job Title Goes Here</p><p class="lorem">Lorem ipsum dolor sit amet, consectetur adipiscing elit. Vivamus eu dui ex. Curabitur dapibus dignissim dui.</p></div>
  <div class="portrait" style="left:140px;top:38px" role="img" aria-label="Team member portrait"></div>
  <div class="team-card" style="left:181px;top:38px"><p class="person-name">Name<br>Goes Here</p><p class="person-role">Job Title Goes Here</p><p class="lorem">Lorem ipsum dolor sit amet, consectetur adipiscing elit. Vivamus eu dui ex. Curabitur dapibus dignissim dui.</p></div>
  <div class="portrait" style="left:223px;top:38px" role="img" aria-label="Team member portrait"></div>
  <div class="portrait" style="left:14px;top:89px;height:49px" role="img" aria-label="Team member portrait"></div>
  <div class="team-card" style="left:56px;top:88px"><p class="person-name t-purple">Name<br>Goes Here</p><p class="person-role">Job Title Goes Here</p><p class="lorem">Lorem ipsum dolor sit amet, consectetur adipiscing elit. Vivamus eu dui ex. Curabitur dapibus dignissim dui.</p></div>
  <div class="portrait" style="left:98px;top:89px;height:49px" role="img" aria-label="Team member portrait"></div>
  <div class="team-card" style="left:140px;top:88px"><p class="person-name t-purple">Name<br>Goes Here</p><p class="person-role">Job Title Goes Here</p><p class="lorem">Lorem ipsum dolor sit amet, consectetur adipiscing elit. Vivamus eu dui ex. Curabitur dapibus dignissim dui.</p></div>
  <div class="portrait" style="left:181px;top:89px;height:49px" role="img" aria-label="Team member portrait"></div>
  <div class="team-card" style="left:223px;top:88px"><p class="person-name t-purple">Name<br>Goes Here</p><p class="person-role">Job Title Goes Here</p><p class="lorem">Lorem ipsum dolor sit amet, consectetur adipiscing elit. Vivamus eu dui ex. Curabitur dapibus dignissim dui.</p></div>
  <div class="footer"><span>© 2021 Corvane Therapeutics. All Rights Reserved.</span><span>7</span></div>
</section>

<!-- 8 bullets + band -->
<section class="slide">
  <h2 class="slide-title">Slide Title Goes Here</h2>
  <div class="brand"><span class="brand-mark"></span><span class="brand-name">Corvane<small>Therapeutics</small></span></div>
  <ul class="bullets lorem abs" style="left:14px;top:32px;width:122px">
    <li>Lorem ipsum dolor sit amet, consectetur adipiscing elit. Vivamus eu dui ex. Curabitur dapibus dignissim dui, in molestie metus feugiat sed.</li>
    <li>Praesent aliquet lorem ex, eu dapibus odio varius at. Duis eget tellus porta, consequat lacus vitae, venenatis dolor.</li>
    <li>Lorem ipsum dolor sit amet, consectetur adipiscing elit. Vivamus eu dui ex. Curabitur dapibus dignissim dui, in molestie metus feugiat sed.</li>
  </ul>
  <div class="photo" style="left:152px;top:33px;width:98px;height:97px;background:linear-gradient(135deg,#9fb4c8,#3f6e9c 55%,#1d3350)" role="img" aria-label="Photo of a scientist reviewing data on screens"></div>
  <div class="abs" style="left:0;top:86px;width:272px;height:39px;background:linear-gradient(90deg,var(--blue) 0%,var(--blue) 45%,var(--purple) 100%);opacity:.95"></div>
  <p class="abs" style="left:24px;top:91px;width:232px;font-size:3.6px;line-height:1.25;color:#fff">Lorem ipsum dolor sit amet, consectetur adipiscing elit. Vivamus eu dui ex. Curabitur dapibus dignissim dui, in molestie metus feugiat sed. Praesent aliquet lorem ex, eu dapibus odio varius at. Duis eget tellus porta, consequat lacus vitae, venenatis dolor. Nulla facilisi. In et sollicitudin lacus. Donec risus orci, gravida sit amet risus vehicula, aliquet pretium sapien. Nullam sit amet magna non ex bibendum mollis. Nunc vel neque eu augue dignissim congue ut vitae magna.</p>
  <div class="footer"><span>© 2021 Corvane Therapeutics. All Rights Reserved.</span><span>8</span></div>
</section>

<!-- 9 features -->
<section class="slide">
  <h2 class="slide-title">Slide Title Goes Here</h2>
  <div class="brand"><span class="brand-mark"></span><span class="brand-name">Corvane<small>Therapeutics</small></span></div>
  <p class="lorem abs center" style="left:20px;top:43px;width:232px;font-size:3.4px">Lorem ipsum dolor sit amet, consectetur adipiscing elit. Vivamus eu dui ex. Curabitur dapibus dignissim dui, in molestie metus feugiat sed. Praesent aliquet lorem ex, eu dapibus odio varius at. Duis eget tellus porta, consequat lacus vitae, venenatis dolor.</p>
  <div class="icon-dot" style="left:35px;top:68px;background:var(--blue)"><svg width="11" height="8" viewBox="0 0 11 8"><path d="M0 1 Q5.5 7 11 1 M0 7 Q5.5 1 11 7" stroke="#fff" fill="none" stroke-width="1"/></svg></div>
  <div class="icon-dot" style="left:95px;top:68px;background:var(--purple)"><svg width="10" height="9" viewBox="0 0 10 9"><path d="M1 4 H9 Q9 8 5 8 Q1 8 1 4Z" fill="#fff"/><line x1="6" y1="4" x2="9" y2="0" stroke="#fff" stroke-width="1"/></svg></div>
  <div class="icon-dot" style="left:155px;top:68px;background:var(--indigo)"><svg width="9" height="10" viewBox="0 0 9 10"><rect x="3" y="0" width="2" height="6" fill="#fff"/><rect x="1" y="8.5" width="7" height="1.2" fill="#fff"/><path d="M2 4 Q0 6 3 8" stroke="#fff" fill="none"/></svg></div>
  <div class="icon-dot" style="left:216px;top:68px;background:var(--crimson)"><svg width="9" height="10" viewBox="0 0 9 10"><path d="M3 0 H6 V3.5 L9 9.5 H0 L3 3.5Z" fill="#fff"/></svg></div>
  <div class="feature" style="left:19px;top:92px"><h4 class="t-blue">Heading</h4><p class="lorem">Lorem ipsum dolor sit amet, consectetur adipiscing elit. Vivamus eu dui ex. Curabitur dapibus dignissim dui, in molestie metus feugiat sed. Praesent aliquet lorem ex, eu dapibus odio varius at.</p></div>
  <div class="feature" style="left:79px;top:92px"><h4 class="t-purple">Heading</h4><p class="lorem">Lorem ipsum dolor sit amet, consectetur adipiscing elit. Vivamus eu dui ex. Curabitur dapibus dignissim dui, in molestie metus feugiat sed. Praesent aliquet lorem ex, eu dapibus odio varius at.</p></div>
  <div class="feature" style="left:139px;top:92px"><h4 class="t-indigo">Heading</h4><p class="lorem">Lorem ipsum dolor sit amet, consectetur adipiscing elit. Vivamus eu dui ex. Curabitur dapibus dignissim dui, in molestie metus feugiat sed. Praesent aliquet lorem ex, eu dapibus odio varius at.</p></div>
  <div class="feature" style="left:200px;top:92px"><h4 class="t-crimson">Heading</h4><p class="lorem">Lorem ipsum dolor sit amet, consectetur adipiscing elit. Vivamus eu dui ex. Curabitur dapibus dignissim dui, in molestie metus feugiat sed. Praesent aliquet lorem ex, eu dapibus odio varius at.</p></div>
  <div class="footer"><span>© 2021 Corvane Therapeutics. All Rights Reserved.</span><span>9</span></div>
</section>

<!-- 10 paragraph + band -->
<section class="slide">
  <h2 class="slide-title">Slide Title Goes Here</h2>
  <div class="brand"><span class="brand-mark"></span><span class="brand-name">Corvane<small>Therapeutics</small></span></div>
  <p class="lorem abs" style="left:14px;top:32px;width:244px">Lorem ipsum dolor sit amet, consectetur adipiscing elit. Vivamus eu dui ex. Curabitur dapibus dignissim dui, in molestie metus feugiat sed. Praesent aliquet lorem ex, eu dapibus odio varius at. Duis eget tellus porta, consequat lacus vitae, venenatis dolor. Nulla facilisi. In et sollicitudin lacus.</p>
  <p class="lorem abs" style="left:14px;top:48px;width:244px">Donec risus orci, gravida sit amet risus vehicula, aliquet pretium sapien. Nullam sit amet magna non ex bibendum mollis. Nunc vel neque eu augue dignissim congue ut vitae magna. Phasellus eget commodo arcu. Nunc vitae semper dui. Integer venenatis, tellus sit amet interdum pretium, erat neque rhoncus turpis.</p>
  <div class="photo" style="left:0;top:71px;width:140px;height:54px;background:linear-gradient(90deg,#dfe4ea,#8fa6c0 50%,#2a4f86)" role="img" aria-label="Photo of a microscope and sample tubes on a lab bench"></div>
  <div class="abs" style="left:140px;top:71px;width:114px;height:54px;background:var(--grad);color:#fff;font-size:6.2px;line-height:1.18;padding:8px 8px 0 8px">Lorem ipsum dolor sit amet, consectetur adipiscing elit. Vivamus eu dui ex. Curabitur dapibus dignissim dui, in molestie metus.</div>
  <div class="footer"><span>© 2021 Corvane Therapeutics. All Rights Reserved.</span><span>10</span></div>
</section>

<!-- 11 three columns -->
<section class="slide">
  <h2 class="slide-title">Slide Title Goes Here</h2>
  <div class="brand"><span class="brand-mark"></span><span class="brand-name">Corvane<small>Therapeutics</small></span></div>
  <div class="abs" style="left:94px;top:44px;width:.5px;height:84px;background:var(--rule)"></div>
  <div class="abs" style="left:177px;top:44px;width:.5px;height:84px;background:var(--rule)"></div>
  <div class="abs" style="left:15px;top:46px;width:74px"><p class="col-head">Title Goes Here!</p><ul class="bullets lorem"><li>Lorem ipsum dolor sit amet, consectetur adipiscing elit. Vivamus eu dui ex. Curabitur dapibus dignissim dui, in molestie metus feugiat sed.</li><li>Praesent aliquet lorem ex, eu dapibus odio varius at. Duis eget tellus porta, consequat lacus vitae, venenatis dolor.</li><li>Nulla facilisi. In et sollicitudin lacus. Donec risus orci, gravida sit amet risus vehicular.</li><li>Nullam sit amet magna non ex bibendum mollis.</li></ul></div>
  <div class="abs" style="left:99px;top:46px;width:74px"><p class="col-head">Title Goes Here!</p><ul class="bullets lorem"><li>Lorem ipsum dolor sit amet, consectetur adipiscing elit. Vivamus eu dui ex. Curabitur dapibus dignissim dui, in molestie metus feugiat sed.</li><li>Praesent aliquet lorem ex, eu dapibus odio varius at. Duis eget tellus porta, consequat lacus vitae, venenatis dolor.</li><li>Nulla facilisi. In et sollicitudin lacus. Donec risus orci, gravida sit amet risus vehicular.</li><li>Nullam sit amet magna non ex bibendum mollis.</li></ul></div>
  <div class="abs" style="left:182px;top:46px;width:74px"><p class="col-head">Title Goes Here!</p><ul class="bullets lorem"><li>Lorem ipsum dolor sit amet, consectetur adipiscing elit. Vivamus eu dui ex. Curabitur dapibus dignissim dui, in molestie metus feugiat sed.</li><li>Praesent aliquet lorem ex, eu dapibus odio varius at. Duis eget tellus porta, consequat lacus vitae, venenatis dolor.</li><li>Nulla facilisi. In et sollicitudin lacus. Donec risus orci, gravida sit amet risus vehicular.</li><li>Nullam sit amet magna non ex bibendum mollis.</li></ul></div>
  <div class="footer"><span>© 2021 Corvane Therapeutics. All Rights Reserved.</span><span>11</span></div>
</section>

<!-- 12 dense text -->
<section class="slide">
  <h2 class="slide-title">Slide Title Goes Here</h2>
  <div class="brand"><span class="brand-mark"></span><span class="brand-name">Corvane<small>Therapeutics</small></span></div>
  <div class="abs lorem" style="left:14px;top:38px;width:244px;font-size:2.9px;text-align:justify">
    <p style="margin-bottom:2.5px">Lorem ipsum dolor sit amet, consectetur adipiscing elit. Vivamus eu dui ex. Curabitur dapibus dignissim dui, in molestie metus feugiat sed. Praesent aliquet lorem ex, eu dapibus odio varius at. Duis eget tellus porta, consequat lacus vitae, venenatis dolor. Nulla facilisi. In et sollicitudin lacus.</p>
    <p style="margin-bottom:2.5px">Donec risus orci, gravida sit amet risus vehicula, aliquet pretium sapien. Nullam sit amet magna non ex bibendum mollis. Nunc vel neque eu augue dignissim congue ut vitae magna. Phasellus eget commodo arcu. Nunc vitae semper dui. Integer venenatis, tellus sit amet interdum pretium, erat neque rhoncus turpis, a aliquam augue ligula eget erat.</p>
    <p style="margin-bottom:2.5px">Nunc placerat, arcu nec mattis fermentum, nisi mauris convallis nunc, ut luctus nunc nisl id ex. Nam semper tristique mauris, et vestibulum leo fringilla vel. Nulla id augue eleifend, egestas ligula et, consequat massa. Pellentesque habitant morbi tristique senectus et netus et malesuada fames ac turpis egestas.</p>
    <p style="margin-bottom:2.5px">Lorem ipsum dolor sit amet, consectetur adipiscing elit. Vivamus eu dui ex. Curabitur dapibus dignissim dui, in molestie metus feugiat sed. Praesent aliquet lorem ex, eu dapibus odio varius at. Duis eget tellus porta, consequat lacus vitae, venenatis dolor. Nulla facilisi.</p>
    <p style="margin-bottom:2.5px">In et sollicitudin lacus. Donec risus orci, gravida sit amet risus vehicula, aliquet pretium sapien, erat neque rhoncus turpis, a aliquam augue ligula eget erat. Nunc placerat, arcu nec mattis fermentum, nisi mauris convallis nunc. Phasellus eget commodo arcu.</p>
    <p>Nunc vitae semper dui. Integer venenatis, tellus sit amet interdum pretium, erat neque rhoncus turpis, a aliquam augue ligula eget erat. Nunc placerat, arcu nec mattis fermentum, nisi mauris convallis nunc, ut luctus nunc nisl id ex. Nam semper tristique mauris, et vestibulum leo fringilla vel. Pellentesque habitant morbi tristique senectus et netus et malesuada fames ac turpis egestas.</p>
  </div>
  <div class="footer"><span>© 2021 Corvane Therapeutics. All Rights Reserved.</span><span>12</span></div>
</section>

<!-- 13 timeline -->
<section class="slide">
  <h2 class="slide-title">Slide Title Goes Here</h2>
  <div class="brand"><span class="brand-mark"></span><span class="brand-name">Corvane<small>Therapeutics</small></span></div>
  <div class="abs" style="left:14px;top:85px;width:244px;height:.6px;background:var(--rule)"></div>
  <div class="step" style="left:26px;top:79px;background:var(--blue)">1</div>
  <div class="step" style="left:67px;top:79px;background:var(--purple)">2</div>
  <div class="step" style="left:109px;top:79px;background:var(--indigo)">3</div>
  <div class="step" style="left:150px;top:79px;background:var(--crimson)">4</div>
  <div class="step" style="left:192px;top:79px;background:var(--purple)">5</div>
  <div class="step" style="left:233px;top:79px;background:var(--crimson)">6</div>
  <ul class="ticks abs" style="left:57px;top:41px;width:32px"><li>Lorem ipsum dolor sit amet.</li><li>Vivamus eu dui ex. Curabitur dapibus.</li></ul>
  <p class="step-label t-purple" style="left:53px;top:64px">Heading<br>Goes Here!</p>
  <ul class="ticks abs" style="left:140px;top:41px;width:32px"><li>Lorem ipsum dolor sit amet.</li><li>Vivamus eu dui ex. Curabitur dapibus.</li></ul>
  <p class="step-label t-crimson" style="left:136px;top:64px">Heading<br>Goes Here!</p>
  <ul class="ticks abs" style="left:223px;top:41px;width:32px"><li>Lorem ipsum dolor sit amet.</li><li>Vivamus eu dui ex. Curabitur dapibus.</li></ul>
  <p class="step-label t-crimson" style="left:219px;top:64px">Heading<br>Goes Here!</p>
  <p class="step-label t-blue" style="left:12px;top:95px">Heading<br>Goes Here!</p>
  <ul class="ticks abs" style="left:18px;top:107px;width:32px"><li>Lorem ipsum dolor sit amet.</li><li>Vivamus eu dui ex. Curabitur dapibus.</li></ul>
  <p class="step-label t-indigo" style="left:95px;top:95px">Heading<br>Goes Here!</p>
  <ul class="ticks abs" style="left:101px;top:107px;width:32px"><li>Lorem ipsum dolor sit amet.</li><li>Vivamus eu dui ex. Curabitur dapibus.</li></ul>
  <p class="step-label t-crimson" style="left:178px;top:95px">Heading<br>Goes Here!</p>
  <ul class="ticks abs" style="left:184px;top:107px;width:32px"><li>Lorem ipsum dolor sit amet.</li><li>Vivamus eu dui ex. Curabitur dapibus.</li></ul>
  <div class="footer"><span>© 2021 Corvane Therapeutics. All Rights Reserved.</span><span>13</span></div>
</section>

<!-- 14 section -->
<section class="slide">
  <svg class="abs" width="272" height="153" viewBox="0 0 272 153">
    <defs><linearGradient id="sectionPhoto" x1="0" y1="0" x2="1" y2="1"><stop offset="0" stop-color="#7e8fa6"/><stop offset=".6" stop-color="#c3c7cf"/><stop offset="1" stop-color="#59677c"/></linearGradient></defs>
    <rect x="60" y="0" width="212" height="153" fill="url(#sectionPhoto)" role="img" aria-label="Photo of hands using a tablet in an office"/>
    <polygon points="68,0 150,0 212,58 160,76" fill="#b70ff0" opacity=".85"/>
    <polygon points="86,153 160,76 205,100 165,153" fill="#1e8cff" opacity=".85"/>
    <polygon points="0,0 68,0 160,76 86,153 0,153" fill="#fff"/>
  </svg>
  <h2 class="abs t-blue" style="left:16px;top:53px;font-size:13px;line-height:1.05;font-weight:400">Section Title<br>Goes Here!</h2>
  <p class="abs" style="left:16px;top:85px;width:80px;font-size:3.8px;line-height:1.25;color:var(--body)">Lorem ipsum dolor sit amet, consectetur adipiscing elit.</p>
</section>

<!-- 15 column chart -->
<section class="slide">
  <h2 class="slide-title">Column Chart Slide</h2>
  <div class="brand"><span class="brand-mark"></span><span class="brand-name">Corvane<small>Therapeutics</small></span></div>
  <svg class="abs" style="left:15px;top:45px" width="150" height="82" viewBox="0 0 150 82" role="img" aria-label="Column chart comparing six series across groups A, B and C">
    <g stroke="#e6e7ea" stroke-width=".5"><line x1="1" y1="0" x2="1" y2="72"/><line x1="48" y1="0" x2="48" y2="72"/><line x1="96" y1="0" x2="96" y2="72"/><line x1="144" y1="0" x2="144" y2="72"/></g>
    <g>
      <rect x="6" y="18.25" width="3" height="53.75" fill="#1e8cff"/><rect x="12" y="42" width="3" height="30" fill="#b70ff0"/><rect x="18" y="47" width="3" height="25" fill="#4e6fe8"/><rect x="24" y="19.5" width="3" height="52.5" fill="#d9416f"/><rect x="30" y="57" width="3" height="15" fill="#b70ff0"/><rect x="36" y="32" width="3" height="40" fill="#d9416f"/>
      <rect x="54" y="40.75" width="3" height="31.25" fill="#1e8cff"/><rect x="60" y="17" width="3" height="55" fill="#b70ff0"/><rect x="66" y="47" width="3" height="25" fill="#4e6fe8"/><rect x="72" y="40.75" width="3" height="31.25" fill="#d9416f"/><rect x="78" y="7" width="3" height="65" fill="#d9416f"/><rect x="84" y="38.25" width="3" height="33.75" fill="#b70ff0"/>
      <rect x="102" y="28.25" width="3" height="43.75" fill="#1e8cff"/><rect x="108" y="49.5" width="3" height="22.5" fill="#b70ff0"/><rect x="114" y="34.5" width="3" height="37.5" fill="#4e6fe8"/><rect x="120" y="44.5" width="3" height="27.5" fill="#d9416f"/><rect x="126" y="44.5" width="3" height="27.5" fill="#d9416f"/><rect x="132" y="57" width="3" height="15" fill="#b70ff0"/>
    </g>
    <line x1="1" y1="72" x2="144" y2="72" stroke="#c9ccd2" stroke-width=".5"/>
    <g font-family="Montserrat, sans-serif" font-size="3" fill="#888" text-anchor="middle"><text x="24" y="78">A</text><text x="72" y="78">B</text><text x="120" y="78">C</text></g>
  </svg>
  <div class="abs" style="left:175px;top:50px;width:82px">
    <p style="font-size:4.4px;font-weight:500">Title Goes Here!</p><p class="lorem" style="font-size:2.6px;margin-bottom:8px">Lorem ipsum dolor sit amet, consectetur adipiscing elit. Vivamus eu dui ex. Curabitur dapibus dignissim dui.</p>
    <p style="font-size:4.4px;font-weight:500">Title Goes Here!</p><p class="lorem" style="font-size:2.6px;margin-bottom:8px">Lorem ipsum dolor sit amet, consectetur adipiscing elit. Vivamus eu dui ex. Curabitur dapibus dignissim dui.</p>
    <p style="font-size:4.4px;font-weight:500">Title Goes Here!</p><p class="lorem" style="font-size:2.6px">Lorem ipsum dolor sit amet, consectetur adipiscing elit. Vivamus eu dui ex. Curabitur dapibus dignissim dui.</p>
  </div>
  <div class="footer"><span>© 2021 Corvane Therapeutics. All Rights Reserved.</span><span>15</span></div>
</section>

<!-- 16 pie chart -->
<section class="slide">
  <h2 class="slide-title">Pie Chart Slide</h2>
  <div class="brand"><span class="brand-mark"></span><span class="brand-name">Corvane<small>Therapeutics</small></span></div>
  <div class="abs" style="left:12px;top:51px;width:248px;height:34px;background:var(--panel)"></div>
  <div class="abs" style="left:12px;top:88px;width:248px;height:32px;background:var(--panel)"></div>
  <div class="side-tab" style="left:0;top:51px;height:34px;background:var(--crimson)"><span>20%</span></div>
  <div class="side-tab" style="left:0;top:88px;height:32px;background:var(--indigo)"><span>40%</span></div>
  <div class="side-tab" style="left:260px;top:51px;height:34px;background:var(--blue)"><span>80%</span></div>
  <div class="side-tab" style="left:260px;top:88px;height:32px;background:var(--purple)"><span>60%</span></div>
  <div class="pie-note" style="left:17px;top:56px"><h4 class="t-crimson">Heading</h4><p class="lorem">Lorem ipsum dolor sit amet, consectetur adipiscing elit. Vivamus eu dui ex. Curabitur dapibus dignissim dui.</p></div>
  <div class="pie-note" style="left:17px;top:93px"><h4 class="t-indigo">Heading</h4><p class="lorem">Lorem ipsum dolor sit amet, consectetur adipiscing elit. Vivamus eu dui ex. Curabitur dapibus dignissim dui.</p></div>
  <div class="pie-note" style="left:203px;top:56px;margin-left:-36px"><h4 class="t-blue">Heading</h4><p class="lorem">Lorem ipsum dolor sit amet, consectetur adipiscing elit. Vivamus eu dui ex. Curabitur dapibus dignissim dui.</p></div>
  <div class="pie-note" style="left:203px;top:93px;margin-left:-36px"><h4 class="t-purple">Heading</h4><p class="lorem">Lorem ipsum dolor sit amet, consectetur adipiscing elit. Vivamus eu dui ex. Curabitur dapibus dignissim dui.</p></div>
  <svg class="abs" style="left:91px;top:40px" width="90" height="90" viewBox="-45 -45 90 90" role="img" aria-label="Pie chart with four segments">
    <circle r="45" fill="#fff"/>
    <g stroke="#fff" stroke-width="1">
      <path d="M0 0 L0 -41 A41 41 0 0 1 26.35 31.41 Z" fill="#1e8cff"/>
      <path d="M0 0 L26.35 31.41 A41 41 0 0 1 -33.58 23.52 Z" fill="#b70ff0"/>
      <path d="M0 0 L-33.58 23.52 A41 41 0 0 1 -35.51 -20.5 Z" fill="#4e6fe8"/>
      <path d="M0 0 L-35.51 -20.5 A41 41 0 0 1 0 -41 Z" fill="#d9416f"/>
    </g>
    <g font-family="Montserrat, sans-serif" font-size="4.4" fill="#fff" font-weight="500" text-anchor="middle">
      <text x="22" y="2">80%</text><text x="-8" y="35">60%</text><text x="-27" y="2">40%</text><text x="-11" y="-28">20%</text>
    </g>
  </svg>
  <div class="footer"><span>© 2021 Corvane Therapeutics. All Rights Reserved.</span><span>16</span></div>
</section>

<!-- 17 rings -->
<section class="slide">
  <h2 class="slide-title">Slide Title Goes Here!</h2>
  <div class="brand"><span class="brand-mark"></span><span class="brand-name">Corvane<small>Therapeutics</small></span></div>
  <svg class="abs" style="left:0;top:40px" width="272" height="62" viewBox="0 0 272 62" role="img" aria-label="Progress rings at 64, 82 and 94 percent">
    <g fill="none" stroke-width="2.4">
      <circle cx="60" cy="30" r="24" stroke="#eef0f3"/>
      <circle cx="60" cy="30" r="24" stroke="#1e8cff" stroke-dasharray="96.5 150.8" transform="rotate(-90 60 30)"/>
      <circle cx="136" cy="30" r="24" stroke="#eef0f3"/>
      <circle cx="136" cy="30" r="24" stroke="#b70ff0" stroke-dasharray="123.7 150.8" transform="rotate(-90 136 30)"/>
      <circle cx="211" cy="30" r="24" stroke="#eef0f3"/>
      <circle cx="211" cy="30" r="24" stroke="#4e6fe8" stroke-dasharray="141.8 150.8" transform="rotate(-90 211 30)"/>
    </g>
    <g font-family="Montserrat, sans-serif" font-size="9" text-anchor="middle" font-weight="500">
      <text x="60" y="33" fill="#1e8cff">64<tspan font-size="6">%</tspan></text>
      <text x="136" y="33" fill="#b70ff0">82<tspan font-size="6">%</tspan></text>
      <text x="211" y="33" fill="#4e6fe8">94<tspan font-size="6">%</tspan></text>
    </g>
  </svg>
  <div class="feature" style="left:32px;top:105px;width:56px"><h4 class="t-blue" style="font-size:6px">Heading</h4><p class="lorem">Lorem ipsum dolor sit amet, at laoreet nibh duis mauris. Per ultrices lectus sed metus tristique eu. Lorem ipsum dolor.</p></div>
  <div class="feature" style="left:108px;top:105px;width:56px"><h4 class="t-purple" style="font-size:6px">Heading</h4><p class="lorem">Lorem ipsum dolor sit amet, at laoreet nibh duis mauris. Per ultrices lectus sed metus tristique eu. Lorem ipsum dolor.</p></div>
  <div class="feature" style="left:183px;top:105px;width:56px"><h4 class="t-indigo" style="font-size:6px">Heading</h4><p class="lorem">Lorem ipsum dolor sit amet, at laoreet nibh duis mauris. Per ultrices lectus sed metus tristique eu. Lorem ipsum dolor.</p></div>
  <div class="footer"><span>© 2021 Corvane Therapeutics. All Rights Reserved.</span><span>17</span></div>
</section>

<!-- 18 process -->
<section class="slide">
  <h2 class="slide-title">Process Slide</h2>
  <div class="brand"><span class="brand-mark"></span><span class="brand-name">Corvane<small>Therapeutics</small></span></div>
  <div class="abs" style="left:5px;top:60px;width:262px;border-top:.6px dashed #d6d8dd"></div>
  <div class="step" style="left:47px;top:53px;width:15px;height:15px;font-size:7.5px;background:var(--blue)">1</div>
  <div class="step" style="left:101px;top:53px;width:15px;height:15px;font-size:7.5px;background:var(--purple)">2</div>
  <div class="step" style="left:156px;top:53px;width:15px;height:15px;font-size:7.5px;background:var(--indigo)">3</div>
  <div class="step" style="left:210px;top:53px;width:15px;height:15px;font-size:7.5px;background:var(--crimson)">4</div>
  <div class="feature" style="left:30px;top:81px;width:48px"><h4 class="t-blue" style="font-size:5.4px;line-height:1.05">Title Goes<br>Here!</h4><p class="lorem">Lorem ipsum dolor sit amet, consectetur adipiscing elit. Vivamus eu dui ex. Curabitur dapibus dignissim dui.</p></div>
  <div class="feature" style="left:84px;top:81px;width:48px"><h4 class="t-purple" style="font-size:5.4px;line-height:1.05">Title Goes<br>Here!</h4><p class="lorem">Lorem ipsum dolor sit amet, consectetur adipiscing elit. Vivamus eu dui ex. Curabitur dapibus dignissim dui.</p></div>
  <div class="feature" style="left:139px;top:81px;width:48px"><h4 class="t-indigo" style="font-size:5.4px;line-height:1.05">Title Goes<br>Here!</h4><p class="lorem">Lorem ipsum dolor sit amet, consectetur adipiscing elit. Vivamus eu dui ex. Curabitur dapibus dignissim dui.</p></div>
  <div class="feature" style="left:193px;top:81px;width:48px"><h4 class="t-crimson" style="font-size:5.4px;line-height:1.05">Title Goes<br>Here!</h4><p class="lorem">Lorem ipsum dolor sit amet, consectetur adipiscing elit. Vivamus eu dui ex. Curabitur dapibus dignissim dui.</p></div>
  <div class="footer"><span>© 2021 Corvane Therapeutics. All Rights Reserved.</span><span>18</span></div>
</section>

<!-- 19 table -->
<section class="slide">
  <h2 class="slide-title">Table Slide</h2>
  <div class="brand"><span class="brand-mark"></span><span class="brand-name">Corvane<small>Therapeutics</small></span></div>
  <table class="table">
    <tr>
      <th rowspan="3" style="background:var(--navy);color:#fff;font-size:9px;font-weight:500;text-align:left;padding-left:3px;line-height:1.05;width:58px">Title Goes<br>Here!</th>
      <th style="background:var(--blue);color:#fff;font-weight:400;height:9px">Heading 1</th>
      <th style="background:var(--purple);color:#fff;font-weight:400">Heading 2</th>
      <th style="background:var(--blue);color:#fff;font-weight:400">Heading 3</th>
    </tr>
    <tr>
      <td style="background:var(--blue);color:#fff;font-size:9px;font-weight:500;height:14px">2019</td>
      <td style="background:var(--purple);color:#fff;font-size:9px;font-weight:500">2020</td>
      <td style="background:var(--blue);color:#fff;font-size:9px;font-weight:500">2021</td>
    </tr>
    <tr>
      <td style="background:var(--blue);color:#fff;font-size:2.4px;height:6px">Text Goes Here</td>
      <td style="background:var(--purple);color:#fff;font-size:2.4px">Text Goes Here</td>
      <td style="background:var(--blue);color:#fff;font-size:2.4px">Text Goes Here</td>
    </tr>
    <tr class="row"><td>Text Goes Here</td><td class="tick-b">✓</td><td class="tick-p">✓</td><td class="tick-b">✓</td></tr>
    <tr class="row"><td>Text Goes Here</td><td class="tick-b">✓</td><td class="tick-p">✓</td><td class="tick-b">✓</td></tr>
    <tr class="row"><td>Text Goes Here</td><td class="tick-b">✓</td><td class="tick-p">✓</td><td class="tick-b">✓</td></tr>
    <tr class="row"><td>Text Goes Here</td><td></td><td class="tick-p">✓</td><td class="tick-b">✓</td></tr>
    <tr class="row"><td>Text Goes Here</td><td></td><td></td><td class="tick-b">✓</td></tr>
    <tr>
      <td style="background:var(--navy);height:8px"></td>
      <td style="background:var(--blue);color:#fff;font-size:2.6px">Text Goes Here</td>
      <td style="background:var(--purple);color:#fff;font-size:2.6px">Text Goes Here</td>
      <td style="background:var(--blue);color:#fff;font-size:2.6px">Text Goes Here</td>
    </tr>
  </table>
  <div class="footer"><span>© 2021 Corvane Therapeutics. All Rights Reserved.</span><span>19</span></div>
</section>

<!-- 20 quotes -->
<section class="slide">
  <h2 class="slide-title">Slide Title Goes Here</h2>
  <div class="brand"><span class="brand-mark"></span><span class="brand-name">Corvane<small>Therapeutics</small></span></div>
  <div class="photo" style="left:0;top:41px;width:91px;height:89px;background:linear-gradient(135deg,#d5d9de,#8e9aaa 55%,#4d5a6c)" role="img" aria-label="Photo of hands holding a tablet"></div>
  <div class="quote-box" style="left:96px;background:var(--blue)"><div class="mark">“</div><p>Lorem ipsum dolor sit amet, consectetur adipiscing elit. Vivamus eu dui ex. Curabitur dapibus dignissim dui, in molestie metus feugiat sed. Praesent aliquet lorem ex, eu dapibus odio varius at.</p></div>
  <div class="quote-box" style="left:181px;background:var(--purple)"><div class="mark">“</div><p>Lorem ipsum dolor sit amet, consectetur adipiscing elit. Vivamus eu dui ex. Curabitur dapibus dignissim dui, in molestie metus feugiat sed. Praesent aliquet lorem ex, eu dapibus odio varius at.</p></div>
  <div class="footer"><span>© 2021 Corvane Therapeutics. All Rights Reserved.</span><span>20</span></div>
</section>

<!-- 21 contact -->
<section class="slide" style="background:var(--dark)">
  <svg class="abs" width="272" height="153" viewBox="0 0 272 153">
    <defs><linearGradient id="contactPhoto" x1="0" y1="0" x2="1" y2="1"><stop offset="0" stop-color="#2a2b30"/><stop offset=".6" stop-color="#55585f"/><stop offset="1" stop-color="#1d1e22"/></linearGradient></defs>
    <rect x="110" y="0" width="162" height="153" fill="url(#contactPhoto)" role="img" aria-label="Black and white photo of city towers seen from below"/>
    <polygon points="0,0 108,0 200,78 130,153 0,153" fill="#17181c"/>
    <polygon points="108,0 155,0 215,78 200,78" fill="#1e8cff" opacity=".75"/>
    <polygon points="130,153 200,78 215,78 160,153" fill="#1e8cff" opacity=".35"/>
  </svg>
  <div class="cover-brand" style="left:26px;top:57px;color:#fff"><span class="brand-mark"></span><span class="brand-name">Corvane<small>Therapeutics</small></span></div>
  <h3 class="abs" style="left:26px;top:85px;font-size:7px;font-weight:500;color:#fff">Contact Us</h3>
  <p class="abs" style="left:26px;top:96px;font-size:3px;color:#ddd">Insert Company Address Here!</p>
  <ul class="abs" style="left:26px;top:105px;list-style:none;font-size:3px;color:#ddd;line-height:7.5px">
    <li><svg width="4" height="4" viewBox="0 0 10 10"><path d="M2 0 L4 3 L3 4 Q4 6 6 7 L7 6 L10 8 L8 10 Q0 9 0 2Z" fill="#ddd"/></svg> &nbsp;Insert Phone Number</li>
    <li><svg width="4" height="4" viewBox="0 0 10 10"><circle cx="5" cy="5" r="2" fill="none" stroke="#ddd" stroke-width="1.4"/><path d="M7 3 V6 Q7 8 9 7 Q10 2 5 1 Q0 1 1 6 Q2 10 7 9" fill="none" stroke="#ddd" stroke-width="1.2"/></svg> &nbsp;Insert E-Mail Address</li>
    <li><svg width="4" height="4" viewBox="0 0 10 10"><circle cx="5" cy="5" r="4.3" fill="none" stroke="#ddd"/><ellipse cx="5" cy="5" rx="2" ry="4.3" fill="none" stroke="#ddd"/><line x1="1" y1="5" x2="9" y2="5" stroke="#ddd"/></svg> &nbsp;Insert URL Address</li>
  </ul>
  <p class="abs" style="left:0;width:272px;top:141px;text-align:center;font-size:2.2px;color:#aaa;padding-left:60px">© 2021 Corvane Therapeutics. All Rights Reserved.</p>
</section>

</main>
</body>
</html>
```